I want ideas sample designs for my book cover

Hello,

We need a book cover designed in flat and 3D Versions. We would like to have jpg and png for final output and include a copy of the PSD for future revisions.

Here are the basic details:

Title: The Harvest of Quiet Builders
Author: Norman Quillfeather

Dimensions of book:

Was looking at the Pavo website for dimensions. I thought you may want to go on there and look at the different sizes. I used the 6x9” perfect bound US trade size for my book. You will see that this has a spine width of 0.225”, Cover size of 12.48 x 9.25” and spine begins at 6.125”

If you need background info on the author just to get an idea what he does, please check:

http://NormanQuillfeather.example

IMPORTANT: Please see attached document for a more detailed info:

Exact Title Of book
Back Cover
Spine Info
Measurements of book and dimension
Examples of book covers
Norman's photo attached

Thanks,
Darlene

Industry/Entity Type

Life Coaching

Font styles to use
Serif

Requirements
Must have
• Jpg, png and PSD files
• title
• author
• exact dimensions
• front and back cover
• flat and 3d versions

```html
<!DOCTYPE html>
<html lang="en">
<head>
<meta charset="utf-8">
<title>The Harvest of Quiet Builders – Full Cover</title>
<link rel="stylesheet" href="https://fonts.googleapis.com/css2?family=Anton&family=Source+Sans+3:ital,wght@0,400;0,700;1,400&display=swap">
<style>
  :root{
    --orange:#f26b21;
    --black:#000;
    --white:#fff;
    --ink:#111;
    --sky-top:#c4d8e7;
    --sky-low:#e6edf2;
    --sea:#2a5f95;
    --sea-deep:#15284a;
  }
  *{margin:0;padding:0;box-sizing:border-box}
  html,body{width:1200px;height:893px;overflow:hidden;background:var(--black)}
  .cover{position:relative;width:1200px;height:893px;background:var(--black);font-family:"Source Sans 3","Myriad Pro",Arial,sans-serif}

  .back-panel{position:absolute;left:0;top:0;width:610px;height:604px;background:var(--orange)}
  .blurb{position:absolute;left:38px;top:38px;width:512px;color:var(--ink);font-size:13.4px;line-height:17.4px;text-align:justify;hyphens:auto}
  .blurb p{margin-bottom:17.4px}

  .spine-title{position:absolute;left:589px;top:134px;writing-mode:vertical-rl;color:var(--ink);font-size:13px;letter-spacing:2.6px;white-space:nowrap}
  .spine-photo{position:absolute;left:588px;top:605px;width:22px;height:27px;background:linear-gradient(#ddd,#888)}
  .spine-author{position:absolute;left:591px;top:730px;writing-mode:vertical-rl;color:var(--white);font-size:13px;white-space:nowrap}

  .front-photo{position:absolute;left:610px;top:0;width:590px;height:604px;
    background:linear-gradient(180deg,var(--sky-top) 0%,var(--sky-low) 52%,var(--sea) 62%,var(--sea-deep) 100%)}
  .series-line{position:absolute;left:700px;top:26px;width:420px;text-align:center;color:var(--ink);font-size:19px}
  .series-line b{font-weight:700}
  .front-author{position:absolute;left:660px;top:46px;width:490px;text-align:center;color:var(--orange);font-weight:700;font-size:47px;line-height:56px;white-space:nowrap;text-shadow:2px 2px 3px rgba(0,0,0,.35)}
  .promise{position:absolute;left:718px;top:400px;width:320px;text-align:center;color:var(--white);font-size:21px;line-height:27.6px}

  .author-photo{position:absolute;left:37px;top:610px;width:166px;height:166px;background:linear-gradient(135deg,#f2f2f2,#b5b5b5)}
  .bio{position:absolute;left:217px;top:606px;width:333px;color:var(--white);font-size:11.6px;line-height:14.9px;text-align:justify;hyphens:auto}
  .website{position:absolute;left:60px;top:815px;color:var(--white);font-style:italic;font-size:11.5px}
  .isbn{position:absolute;left:326px;top:782px;width:147px;height:71px;background:var(--white);color:var(--ink);font-size:8px;text-align:center;padding-top:4px}

  .title{position:absolute;right:44px;top:612px;color:var(--orange);font-family:"Anton",Impact,sans-serif;font-weight:400;text-align:right;line-height:104px;transform:scaleX(.8);transform-origin:right top}
  .title .line{display:block;font-size:114px;white-space:nowrap}
  .title .article{font-size:60px;margin-right:8px}
</style>
</head>
<body>
<main class="cover">
  <section class="back-panel">
    <div class="blurb">
      <p>This path goes way beyond Entrepreneurism! This is a book for the awakening Entrepreneurs who are building businesses for a better world, affecting generations to come. Bringing you disruptive (in a good way) information, to turn you and your business inside-out for maximum acceleration towards your organisational vision, mission and values.</p>
      <p>There is the potential to have a more meaningful life and business by discovering the symbiotic relationship that exists between all beings. You will be empowered to take your life and business to the next level if you answer the call in this book. It will introduce you to the power of Amazonian plant medicine and other entheogens for improving relationships with yourself, your partner and your family, friends, business associates and Mother Earth.</p>
      <p>An entheogen is defined as ‘a substance (usually from a plant, but not always) that is consumed in order to alter one’s state of consciousness or to act as a catalyst towards encounters with other states of being.’ Plant medicine has been successfully used in South America for thousands of years. This ancient wisdom is helping billionaires, industry icons and entrepreneurs to be better leaders, awakening to its potential for allowing deep examination of the psyche which has the ability to heal, eliminate fears and create a new level of success both personally and professionally.</p>
      <p>Norman shares his own heart-felt personal experiences and insights gained from working with these substances and the amazing medicine men and women of the Amazon who retain thousands of years of ancient wisdom. He has spent years turning himself inside-out to powerfully transform his own life and business and wants to encourage entrepreneurs to do the same. He believes that if enough people have the opportunity to explore their own consciousness, then together we can make a positive impact on humanity. If you are ready to travel to the fringes and take a journey within, you will discover that you are the missing link you have been looking for. Get ready to expand your consciousness, transform your business and create a new inspiring lifestyle, which will benefit all beings and our beautiful Mother Earth.</p>
    </div>
  </section>

  <div class="spine-title">The HARVEST OF QUIET BUILDERS</div>
  <div class="spine-photo" role="img" aria-label="Small author portrait on the spine"></div>
  <div class="spine-author">Norman Quillfeather</div>

  <div class="front-photo" role="img" aria-label="Photograph of a man in a dark jacket seen from behind, looking out over the ocean under a bright sky"></div>
  <p class="series-line">From the Best Selling Author of “<b>Lanterns</b>”</p>
  <h2 class="front-author">Norman Quillfeather</h2>
  <p class="promise">How this<br>ANCIENT WISDOM<br>is HELPING billionaires, industry icons and entrepreneurs TO BE BETTER LEADERS, increase impact and leave a legacy</p>

  <div class="author-photo" role="img" aria-label="Black and white portrait of the author smiling"></div>
  <p class="bio">Norman Quillfeather is an internationally-renowned entrepreneur, speaker, philanthropist, thought leader and best-selling author. Having played the role of transformational coach, facilitator and spoken to over three million people from twelve different countries, he challenges you in his second book to journey deep within yourself to examine the core of your true nature and how it impacts your entrepreneurial journey. Some of the world biggest game changers, social entrepreneurs, internet marketers and consultants have reported that Norman’s golden edge is to integrate “purpose with profits” in a way that brings greater meaning to the work they are doing here in the world.</p>
  <p class="website">www.NormanQuillfeather.example</p>
  <div class="isbn">ISBN</div>

  <h1 class="title">
    <span class="line"><span class="article">The</span>HARVEST OF</span>
    <span class="line">QUIET BUILDERS</span>
  </h1>
</main>
</body>
</html>
```